Flyer Tally Your Own Ledger

Hi
Can you please design me a DL Flyer for: Tally Your Own Ledger
Info:
Starting a new Business ?
Want to save on bookkeeping fees for your existing business?

You can now save 1000's off bookkeeping fees by Doing it Yourself.

Using our Bookkeeper software you simply key in the information as you go.

We offer one on one training, backup and support.
We can assist you with BAS Preparation and Payrol Advice.

Add Modules as required:
Point of Sale Module
Jobs Management Module
Website Intergration Module

Fee set up assistance and training.

Lets get the ball rolling: 1300 462 518
www.tyoleg.com.au
admin@tyoleg.com.au (use the logo thing you made)

Target Market(s)

Small Business

Colors
ec1f27
f04a50
f59296
fcdcdc
ffffff

Requirements
Nice to have
• image/s related to bookkeeping

```html
<!DOCTYPE html>
<html lang="en">
<head>
<meta charset="utf-8">
<title>Tally Your Own Ledger – DL Flyer</title>
<link href="https://fonts.googleapis.com/css2?family=Montserrat:wght@800;900&family=Roboto:wght@400;500;700&display=swap" rel="stylesheet">
<style>
  :root{
    --red:#ec1f27;
    --red-soft:#f04a50;
    --red-deep:#b3000f;
    --footer-red:#a6000d;
    --pink:#f59296;
    --blush:#fcdcdc;
    --white:#ffffff;
    --yellow:#ffe11c;
    --ice:#e3eefa;
    --ink:#111111;
    --grey:#555555;
    --stage:#2b0407;
  }
  *{margin:0;padding:0;box-sizing:border-box}
  html,body{width:1200px;height:857px;overflow:hidden}
  body{background:var(--stage);font-family:"Roboto",Arial,sans-serif;position:relative}

  .flyer{position:absolute;left:411px;top:28px;width:377px;height:800px;background:var(--ice);overflow:hidden}

  .hero{position:absolute;left:0;top:0;width:377px;height:372px;
    background:linear-gradient(160deg,var(--red-soft) 0%,var(--red) 45%,var(--red-deep) 100%)}
  .header-curve{position:absolute;left:0;top:0;width:377px;height:110px}

  .brand{position:absolute;left:0;top:36px;width:377px;display:flex;justify-content:center;align-items:center;gap:8px}
  .brand-dot{width:22px;height:22px;border-radius:50%;background:var(--red)}
  .brand-name{font-family:"Roboto",Arial,sans-serif;font-weight:500;font-size:19px;color:var(--red);letter-spacing:.2px}

  .hero-photo{position:absolute;left:192px;top:128px;width:185px;height:244px;
    background:linear-gradient(180deg,rgba(40,50,80,.35) 0%,rgba(30,42,78,.85) 55%,#1e2a4e 100%);
    border-radius:90px 0 0 0}
  .desk{position:absolute;left:0;top:358px;width:377px;height:16px;background:linear-gradient(180deg,#f2f5fa,#dfe7f1)}

  .headline{position:absolute;left:25px;top:138px;font-family:"Montserrat",Arial,sans-serif;font-weight:900;
    font-size:27px;line-height:27.5px;color:var(--yellow);letter-spacing:.3px}
  .subline{position:absolute;left:25px;top:241px;width:160px;font-size:14px;line-height:19.5px;color:var(--white);letter-spacing:.4px}

  .offer-frame{position:absolute;left:43px;top:388px;width:300px;height:53px;border:1.2px solid var(--red)}
  .offer-lead{position:absolute;left:0;top:378px;width:377px;text-align:center;font-size:14px;color:var(--ink)}
  .offer-lead span,.offer-tail span{background:var(--ice);padding:0 12px}
  .offer-main{position:absolute;left:0;top:395px;width:377px;text-align:center;font-family:"Montserrat",Arial,sans-serif;
    font-weight:900;font-size:29px;color:var(--red);letter-spacing:.3px}
  .offer-tail{position:absolute;left:0;top:430px;width:377px;text-align:center;font-size:14px;color:var(--ink)}

  .details{position:absolute;left:0;top:462px;width:377px;text-align:center;font-size:10.3px;line-height:15.5px;color:var(--ink)}
  .details p+p{margin-top:2px}

  .modules{position:absolute;left:16px;top:524px;width:346px;height:104px;background:var(--red);padding:0 10px}
  .modules-title{height:32px;line-height:33px;text-align:center;font-family:"Montserrat",Arial,sans-serif;font-weight:900;
    font-size:15.5px;color:var(--yellow);letter-spacing:.2px}
  .module-row{display:flex;gap:7px}
  .module{flex:1;height:61px;background:var(--white);display:flex;align-items:center;justify-content:center;text-align:center;
    font-weight:700;font-size:9.8px;line-height:12.8px;letter-spacing:.5px;color:var(--ink)}

  .setup{position:absolute;left:0;top:646px;width:377px;text-align:center;padding-right:10px;font-family:"Montserrat",Arial,sans-serif;
    font-weight:900;font-size:17px;line-height:22px;color:var(--ink)}
  .rolling{position:absolute;left:0;top:698px;width:377px;text-align:center;font-size:9.6px;letter-spacing:.8px;color:var(--grey)}

  .footer{position:absolute;left:0;top:720px;width:377px;height:80px;background:var(--footer-red)}
  .phone{position:absolute;left:0;top:10px;width:377px;display:flex;justify-content:center;align-items:center;gap:6px}
  .phone-icon{width:32px;height:32px}
  .phone-number{font-family:"Roboto",Arial,sans-serif;font-weight:700;font-size:37px;color:var(--white);letter-spacing:.5px}
  .links{position:absolute;left:0;top:56px;width:377px;display:flex;justify-content:center;gap:14px;font-weight:700;font-size:10px;color:var(--white)}
  .links span{display:flex;align-items:center;gap:3px}
  .links svg{width:12px;height:12px}
</style>
</head>
<body>
<main class="flyer">
  <section class="hero">
    <svg class="header-curve" viewBox="0 0 377 110" preserveAspectRatio="none" aria-hidden="true">
      <path d="M0 0H377V18C300 70 240 98 188 98C130 98 60 80 0 38Z" fill="#ffffff"/>
      <path d="M0 38C60 80 130 98 188 98C240 98 300 70 377 18V24C300 78 240 104 188 104C130 104 60 88 0 44Z" fill="#ec1f27"/>
    </svg>
    <div class="brand"><span class="brand-dot"></span><span class="brand-name">Tally Your Own Ledger</span></div>

    <div class="hero-photo" role="img" aria-label="Photo of a business owner in a suit reading a tablet at a desk"></div>
    <div class="desk"></div>

    <h1 class="headline">STARTING<br>A NEW<br>BUSINESS?</h1>
    <p class="subline">Want to save on bookkeeping fees for your existing business?</p>
  </section>

  <section class="offer">
    <div class="offer-frame"></div>
    <p class="offer-lead"><span>You can now</span></p>
    <p class="offer-main">SAVE 1000'S OFF</p>
    <p class="offer-tail"><span>bookkeeping fees by Doing it Yourself.</span></p>
  </section>

  <section class="details">
    <p>Using our Bookkeeper software you simply key in the<br>information as you go.</p>
    <p>We offer one on one training, backup and support.<br>We can assist you with BAS Preparation and Payrol Advice.</p>
  </section>

  <section class="modules">
    <h2 class="modules-title">ADD MODULES AS REQUIRED</h2>
    <div class="module-row">
      <div class="module">POINT OF<br>SALE MODULE</div>
      <div class="module">JOBS<br>MANAGEMENT<br>MODULE</div>
      <div class="module">WEBSITE<br>INTERGRATION<br>MODULE</div>
    </div>
  </section>

  <p class="setup">FEE SET UP<br>ASSISTANCE AND TRAINING.</p>
  <p class="rolling">LETS GET THE BALL ROLLING</p>

  <footer class="footer">
    <div class="phone">
      <svg class="phone-icon" viewBox="0 0 32 32" aria-hidden="true">
        <circle cx="16" cy="16" r="16" fill="#ffe11c"/>
        <path d="M11 7.5l3 4-1.8 2.3c1.2 2.6 3.3 4.7 5.9 5.9l2.3-1.8 4 3-1.6 3.4c-7.4-.2-13.4-6.2-13.6-13.6z" fill="#a6000d"/>
      </svg>
      <span class="phone-number">1300-462-518</span>
    </div>
    <div class="links">
      <span><svg viewBox="0 0 12 12" aria-hidden="true"><circle cx="6" cy="6" r="5.3" fill="none" stroke="#ffe11c" stroke-width="1.2"/><path d="M.8 6h10.4M6 .8c-2.4 2.8-2.4 7.6 0 10.4M6 .8c2.4 2.8 2.4 7.6 0 10.4" fill="none" stroke="#ffe11c" stroke-width=".9"/></svg>www.tyoleg.com.au</span>
      <span><svg viewBox="0 0 12 12" aria-hidden="true"><circle cx="6" cy="6" r="6" fill="#ffe11c"/><rect x="2.6" y="3.8" width="6.8" height="4.6" fill="none" stroke="#a6000d" stroke-width=".9"/><path d="M2.6 3.8L6 6.6l3.4-2.8" fill="none" stroke="#a6000d" stroke-width=".9"/></svg>admin@tyoleg.com.au</span>
    </div>
  </footer>
</main>
</body>
</html>
```